Card Design for my dog training business Brightpaw Obedience

Need a business card design for my dog training business with my new logo. Want the card to come off professional yet fun. Want it to be very eye catchy as well. I normally have these at vet clinics, pet stores, and groomers. so need it to look better than my competitors.
Target Market(s)
dog owners
Industry/Entity Type
Dog Training
Contact Information for Business Card
needs logo, my name and info
Font styles to use
Serif
Colors
0255a3
ffffff
ec1f27
000000
333333
fbfbfb
Requirements
Must have
- Brightpaw Obedience
- Felix Orland
- 415 903 2276
- info@brightpawobedience.example
- www.brightpawobedience.example

```html
<!DOCTYPE html>
<html lang="en">
<head>
<meta charset="utf-8">
<title>Brightpaw Obedience – Business Card</title>
<link rel="stylesheet" href="https://fonts.googleapis.com/css2?family=Noto+Serif:wght@400;700&family=Crimson+Text:ital@0;1&family=Open+Sans:wght@400&display=swap">
<style>
  :root {
    --stage: #3a3a3a;
    --card: #141414;
    --card-edge: #222222;
    --blue: #0255a3;
    --blue-bright: #1c8ad8;
    --red: #ec1f27;
    --white: #ffffff;
    --text-soft: #c9c9c9;
    --text-dim: #9a9a9a;
    --emboss: #8a8a8a;
  }
  * { margin: 0; padding: 0; box-sizing: border-box; }
  html, body { width: 799px; height: 1200px; overflow: hidden; }
  body {
    background: var(--stage);
    position: relative;
    font-family: "Open Sans", sans-serif;
  }
  .card {
    position: absolute;
    left: 80px;
    width: 640px;
    height: 366px;
    background: var(--card);
    border: 1px solid var(--card-edge);
    box-shadow: 0 12px 30px rgba(0,0,0,0.45);
  }
  .card--front { top: 110px; }
  .card--back { top: 724px; }

  /* front */
  .front-brand {
    position: absolute;
    top: 118px;
    left: 0;
    width: 100%;
    text-align: center;
    font-family: "Noto Serif", serif;
    font-weight: 700;
    font-size: 40px;
    letter-spacing: 1px;
    color: var(--emboss);
  }
  .front-brand .mark {
    display: inline-block;
    width: 18px;
    height: 18px;
    border-radius: 50%;
    background: var(--emboss);
    vertical-align: middle;
    margin-right: 12px;
    position: relative;
    top: -4px;
  }
  .tagline {
    position: absolute;
    top: 222px;
    left: 0;
    width: 100%;
    text-align: center;
    font-family: "Crimson Text", serif;
    font-style: italic;
    font-size: 20px;
    color: var(--text-dim);
  }

  /* back */
  .back-brand {
    position: absolute;
    top: 110px;
    right: 40px;
    width: 220px;
    text-align: center;
    font-family: "Noto Serif", serif;
    font-weight: 700;
    font-size: 30px;
    line-height: 1.15;
    color: var(--blue-bright);
  }
  .back-brand .rule {
    display: block;
    height: 3px;
    background: var(--red);
    margin: 10px auto 0;
    width: 150px;
  }
  .identity {
    position: absolute;
    left: 36px;
    top: 218px;
    display: flex;
    align-items: baseline;
    gap: 12px;
  }
  .person-name {
    font-family: "Noto Serif", serif;
    font-size: 30px;
    color: var(--blue-bright);
  }
  .divider {
    width: 2px;
    height: 26px;
    background: var(--blue-bright);
    align-self: center;
  }
  .person-role {
    font-family: "Noto Serif", serif;
    font-size: 17px;
    color: var(--text-soft);
  }
  .contacts {
    position: absolute;
    left: 36px;
    top: 272px;
    list-style: none;
    display: flex;
    flex-wrap: wrap;
    gap: 10px 22px;
    width: 580px;
    font-size: 16px;
    color: var(--text-soft);
  }
  .contacts li { display: flex; align-items: center; gap: 8px; }
  .contacts svg { width: 15px; height: 15px; fill: var(--blue-bright); }
</style>
</head>
<body>
  <section class="card card--front" aria-label="Card front">
    <div class="front-brand"><span class="mark"></span>Brightpaw Obedience</div>
    <p class="tagline">“Training dogs across Texas one dog at a time.”</p>
  </section>

  <section class="card card--back" aria-label="Card back">
    <div class="back-brand">Brightpaw Obedience<span class="rule"></span></div>

    <div class="identity">
      <span class="person-name">Felix Orland</span>
      <span class="divider"></span>
      <span class="person-role">Dog Trainer</span>
    </div>

    <ul class="contacts">
      <li>
        <svg viewBox="0 0 16 16" aria-hidden="true"><path d="M3.5 1.5l2.5 0 1 3.5-1.6 1.2a8 8 0 0 0 4.4 4.4L11 9l3.5 1v2.5c0 1-1 2-2 2A11 11 0 0 1 1.5 3.5c0-1 1-2 2-2z"/></svg>
        415 903 2276
      </li>
      <li>
        <svg viewBox="0 0 16 16" aria-hidden="true"><path d="M1 3h14v10H1z M1.5 3.5L8 9l6.5-5.5" fill="none" stroke="var(--blue-bright)" stroke-width="1.6"/></svg>
        info@brightpawobedience.example
      </li>
      <li>
        <svg viewBox="0 0 16 16" aria-hidden="true"><circle cx="8" cy="8" r="6.5" fill="none" stroke="var(--blue-bright)" stroke-width="1.5"/><path d="M1.5 8h13M8 1.5c-3 3.5-3 9.5 0 13M8 1.5c3 3.5 3 9.5 0 13" fill="none" stroke="var(--blue-bright)" stroke-width="1.2"/></svg>
        www.brightpawobedience.example
      </li>
    </ul>
  </section>
</body>
</html>
```